Design some Business Cards for Tavro

Thanks to everyone for their efforts. I will just be reviewing the first two entries from each contestant, so I'd suggest withdrawing entries which are not your favorites & going with your best two. Many thanks, Dorian

I was after a double sided business card for tavro.com.au. Tavro is a billing app and website for tradesman and service providers who move from site to site.

Firstly design for Dorian Webb with mobile 0487 555 904 & email demo@tavro.com.au.

Logo is attached, so please work with those colours. I've also included our url if you believe that is worth building in.

I would like the original working files and the business card will need to be produced for 3 different employees when the winner is selected.

Additional TAVRO text files if this helps.

```html
<!DOCTYPE html>
<html lang="en">
<head>
<meta charset="utf-8">
<title>Tavro Business Card</title>
<link href="https://fonts.googleapis.com/css2?family=Open+Sans:wght@400;600&display=swap" rel="stylesheet">
<style>
  :root {
    --page: #ecebe8;
    --card: #ffffff;
    --ink: #2b2b2d;
    --muted: #5c5c60;
    --red: #d1232f;
    --black: #161616;
    --rule: #e7a3a6;
  }
  * { box-sizing: border-box; margin: 0; padding: 0; }
  html, body {
    width: 1200px; height: 912px; overflow: hidden;
    background: var(--page);
    font-family: "Open Sans", Arial, sans-serif;
    color: var(--ink);
  }
  .card {
    position: absolute;
    width: 525px; height: 300px;
    background: var(--card);
    box-shadow: 0 6px 18px rgba(0,0,0,.18);
    overflow: hidden;
  }
  .card--front { left: 70px; top: 130px; }
  .card--back  { left: 605px; top: 480px; }

  .brand {
    position: absolute;
    display: flex; align-items: center; gap: 12px;
  }
  .brand__dot {
    border-radius: 50%;
    border: 3px solid var(--red);
  }
  .brand__name {
    font-weight: 600;
    color: var(--ink);
    letter-spacing: .04em;
    line-height: 1;
  }
  .card--front .brand { right: 40px; top: 38px; }
  .card--front .brand__dot { width: 40px; height: 40px; }
  .card--front .brand__name { font-size: 48px; }

  .contact {
    position: absolute; right: 40px; top: 122px;
    text-align: right; font-size: 12.5px; color: var(--muted);
    line-height: 1.65;
  }
  .contact__row { display: flex; justify-content: flex-end; align-items: center; gap: 6px; }
  .contact__row svg { width: 10px; height: 10px; fill: var(--red); }

  .divider {
    position: absolute; left: 30px; right: 30px; top: 196px;
    height: 1px; background: var(--rule);
  }

  .person {
    position: absolute; left: 40px; top: 208px;
    font-size: 12.5px; color: var(--muted); line-height: 1.45;
  }
  .person__name { font-size: 19px; color: var(--red); line-height: 1.3; }

  .edge {
    position: absolute; left: 0; right: 0; bottom: 0; height: 8px;
    display: flex;
  }
  .edge__dark { flex: 56; background: var(--black); }
  .edge__red  { flex: 44; background: var(--red); }

  .card--back .brand {
    left: 50%; top: 98px; transform: translateX(-50%);
    gap: 22px;
  }
  .card--back .brand__dot { width: 70px; height: 70px; border-width: 4px; }
  .card--back .brand__name { font-size: 76px; }
  .url {
    position: absolute; left: 0; right: 0; top: 206px;
    text-align: center; font-size: 13px; color: var(--ink);
  }
  .url__domain { color: var(--red); }
</style>
</head>
<body>
  <section class="card card--front" aria-label="Card front">
    <div class="brand">
      <span class="brand__dot"></span>
      <span class="brand__name">TAVRO</span>
    </div>

    <div class="contact">
      <div class="contact__row">0487 555 904
        <svg viewBox="0 0 10 10" aria-hidden="true"><path d="M2 0.5 L3.6 2.6 L2.7 3.6 Q3.8 5.9 6.2 7.2 L7.3 6.3 L9.5 7.8 L8.3 9.5 Q2.5 8.5 0.5 1.7 Z"/></svg>
      </div>
      <div class="contact__row">0487 555 917
        <svg viewBox="0 0 10 10" aria-hidden="true"><path d="M2 0.5 L3.6 2.6 L2.7 3.6 Q3.8 5.9 6.2 7.2 L7.3 6.3 L9.5 7.8 L8.3 9.5 Q2.5 8.5 0.5 1.7 Z"/></svg>
      </div>
      <div class="contact__row">demo@tavro.com.au
        <svg viewBox="0 0 10 10" aria-hidden="true"><circle cx="5" cy="5" r="5"/><circle cx="5" cy="5" r="2" fill="#fff"/></svg>
      </div>
    </div>

    <div class="divider"></div>

    <div class="person">
      <div class="person__name">Dorian Webb</div>
      <div class="person__role">Marketing Manager</div>
      <div class="person__address">88 Harbour Lane, Unit 12</div>
      <div class="person__address">Geelong VIC 3220</div>
    </div>

    <div class="edge"><span class="edge__dark"></span><span class="edge__red"></span></div>
  </section>

  <section class="card card--back" aria-label="Card back">
    <div class="brand">
      <span class="brand__dot"></span>
      <span class="brand__name">TAVRO</span>
    </div>
    <p class="url">www.<span class="url__domain">tavro</span>.com.au</p>
  </section>
</body>
</html>
```